e-commerce store for sport clothing online store "baseball merchandise "web application...

I want to design a UX/UI for my web application website for the online store I will provide you with the following:
1. screen shots of the initial design for the pages>
2. the logo files.
3. The brand guideline file.

the provided files (screen shots) is guideline I want to see CREATIVITY with the UX/UI DESIGN.
PS. PLEASE FOLLOW THE BRANDGUIDE LINE CAREFULLY SPECIALLY THE TYPOGRAPHY & THE COLOR CODES.

PLEASE VISIT THIS WEBSITE brightlane.varomi-qz.com to see more for the screens.

```html
<!DOCTYPE html>
<html lang="en">
<head>
<meta charset="utf-8">
<title>Checkout – Shipping Details</title>
<link rel="stylesheet" href="https://fonts.googleapis.com/css2?family=Lato:wght@400;700;900&display=swap">
<style>
  :root {
    --navy: #13274a;
    --page: #e9ecf1;
    --white: #ffffff;
    --ink: #111111;
    --muted: #555b66;
    --border: #2b2b2b;
    --line: #13274a;
    --disabled: #9c9c9c;
  }
  * { box-sizing: border-box; margin: 0; padding: 0; }
  html, body {
    width: 1032px; height: 1200px; overflow: hidden;
    background: var(--page);
    font-family: "Lato", Arial, sans-serif;
  }
  .screen {
    position: absolute; left: 257px; top: 24px;
    width: 518px; height: 1151px;
    background: var(--white);
    border-radius: 22px;
    overflow: hidden;
  }
  .app-bar {
    position: absolute; left: 0; top: 0; width: 100%; height: 116px;
    background: var(--navy);
    color: var(--white);
  }
  .app-bar__back { position: absolute; left: 32px; top: 45px; }
  .app-bar__title {
    position: absolute; left: 0; right: 0; top: 42px;
    text-align: center; font-weight: 900; font-size: 24px;
  }
  .stepper { position: absolute; left: 0; top: 0; width: 100%; }
  .stepper__line {
    position: absolute; top: 184px; height: 2px; background: var(--line);
  }
  .step {
    position: absolute; width: 140px; margin-left: -70px; top: 157px;
    text-align: center; color: var(--navy);
  }
  .step__dot {
    width: 55px; height: 55px; margin: 0 auto;
    border-radius: 50%; border: 2px solid var(--navy);
    background: var(--white);
    font-weight: 900; font-size: 26px; line-height: 51px;
  }
  .step--active .step__dot { background: var(--navy); color: var(--white); }
  .step__label { margin-top: 8px; font-size: 17px; line-height: 23px; }
  .section-title {
    position: absolute; left: 20px; font-weight: 700; font-size: 21px; color: var(--ink);
  }
  .field {
    position: absolute; height: 68px;
    border: 1.5px solid var(--border); border-radius: 6px;
    padding: 0 13px;
  }
  .field__placeholder {
    display: block; line-height: 65px; font-size: 20px; color: var(--muted);
  }
  .field__label { display: block; margin-top: 8px; font-size: 15px; color: var(--muted); }
  .field__value { display: block; font-size: 21px; color: var(--ink); margin-top: 1px; }
  .col-full { left: 20px; width: 476px; }
  .col-left { left: 20px; width: 228px; }
  .col-right { left: 270px; width: 226px; }
  .action-bar {
    position: absolute; left: 6px; top: 1066px; width: 506px; height: 90px;
    background: var(--white); border-radius: 14px;
    box-shadow: 0 -3px 10px rgba(0,0,0,0.12);
  }
  .button-proceed {
    position: absolute; left: 11px; top: 11px; width: 485px; height: 63px;
    background: var(--disabled); border-radius: 5px;
    color: var(--white); font-weight: 900; font-size: 20px;
    text-align: center; line-height: 63px;
  }
</style>
</head>
<body>
  <main class="screen">
    <header class="app-bar">
      <svg class="app-bar__back" width="26" height="24" viewBox="0 0 26 24" aria-label="Back">
        <path d="M24 12H4M12 3L3 12l9 9" fill="none" stroke="#fff" stroke-width="3" stroke-linecap="round" stroke-linejoin="round"/>
      </svg>
      <h1 class="app-bar__title">Checkout</h1>
    </header>

    <nav class="stepper" aria-label="Checkout steps">
      <div class="stepper__line" style="left:113px;width:293px"></div>
      <div class="step step--active" style="left:113px">
        <div class="step__dot">1</div>
        <div class="step__label">Shipping<br>Details</div>
      </div>
      <div class="step" style="left:258px">
        <div class="step__dot">2</div>
        <div class="step__label">Payment<br>Details</div>
      </div>
      <div class="step" style="left:406px">
        <div class="step__dot">3</div>
        <div class="step__label">Confirmation</div>
      </div>
    </nav>

    <h2 class="section-title" style="top:305px">Deliver to</h2>
    <div class="field col-left" style="top:354px">
      <span class="field__label">First Name*</span><span class="field__value">Rafi</span>
    </div>
    <div class="field col-right" style="top:354px">
      <span class="field__label">Last Name*</span><span class="field__value">Loren</span>
    </div>
    <div class="field col-full" style="top:447px">
      <span class="field__label">Phone*</span><span class="field__value">55501987xx</span>
    </div>

    <h2 class="section-title" style="top:558px">Shipping Address</h2>
    <div class="field col-full" style="top:608px"><span class="field__placeholder">Area*</span></div>
    <div class="field col-left" style="top:700px"><span class="field__placeholder">Block*</span></div>
    <div class="field col-right" style="top:700px"><span class="field__placeholder">Street*</span></div>
    <div class="field col-left" style="top:792px"><span class="field__placeholder">Avenue</span></div>
    <div class="field col-right" style="top:792px"><span class="field__placeholder">Building</span></div>
    <div class="field col-left" style="top:883px"><span class="field__placeholder">Floor</span></div>
    <div class="field col-right" style="top:883px"><span class="field__placeholder">Appartment</span></div>
    <div class="field col-full" style="top:976px"><span class="field__placeholder">Map Location</span></div>

    <div class="action-bar">
      <div class="button-proceed">Proceed</div>
    </div>
  </main>
</body>
</html>
```